Kelvara Pane Works Business Card

We need a business card design that is suitable for a Glazing Business. We Specialize in Repairing broken windows and doors and are a 24hr on call service. We manufacture Shower screens, Fly screens, Wardrobe doors, Security doors and grilles + mirrors. We stock a variety of mesh including Standard mesh, Pet resistant mesh, Tressmet & Clearweft. We would like to use a combination of Light Blue, Dark Blue, Black & White with perhaps a picture of glass breaking.

Industry/Entity Type

Business

Contact Information for Business Card

Narooma Glass Service60B Glasshouse Rocks RdNarooma NSW 2546PH / FAX - 02 44765210MOB - 0419682350 Andrewemail - kelvarapane@fenmail.example

Font styles to use
Serif

Colors
34a7d8
0255a3
ffffff

Requirements
Must have
• logo with picture of broken or cracked glass

```html
<!DOCTYPE html>
<html lang="en">
<head>
<meta charset="utf-8">
<title>Kelvara Pane Works – Business Card</title>
<link rel="stylesheet" href="https://fonts.googleapis.com/css2?family=Open+Sans:wght@400;600;700&display=swap">
<style>
  :root {
    --bg: #e4e4e2;
    --black: #000000;
    --white: #ffffff;
    --light-blue: #34a7d8;
    --sky: #5ec4e6;
    --dark-blue: #0255a3;
    --mid-blue: #3a86c8;
  }
  * { box-sizing: border-box; margin: 0; padding: 0; }
  html, body {
    width: 1200px; height: 900px; overflow: hidden;
    background: var(--bg);
    font-family: "Open Sans", Arial, sans-serif;
  }
  .stage {
    width: 1200px; height: 900px;
    display: flex; flex-direction: column; align-items: center; justify-content: center;
    gap: 48px;
  }
  .card {
    position: relative;
    width: 660px; height: 378px;
    overflow: hidden;
    box-shadow: 0 4px 14px rgba(0,0,0,.18);
  }
  /* Front face */
  .card--front {
    background: var(--black);
    display: flex; flex-direction: column; align-items: center; justify-content: center;
    gap: 30px;
  }
  .brand { display: flex; align-items: center; gap: 16px; }
  .brand__mark {
    width: 30px; height: 30px; border-radius: 50%;
    background: var(--light-blue);
  }
  .brand__name {
    color: var(--light-blue);
    font-weight: 700;
    font-size: 50px;
    letter-spacing: 1px;
    white-space: nowrap;
  }
  .services {
    list-style: none;
    color: var(--white);
    font-weight: 600;
    font-size: 19px;
    text-align: center;
    line-height: 1.5;
  }
  .services li { display: inline-block; margin: 0 7px; }
  .services li::before {
    content: ""; display: inline-block;
    width: 9px; height: 9px; border-radius: 50%;
    background: var(--light-blue);
    margin-right: 6px; vertical-align: 2px;
  }
  /* Back face */
  .card--back { background: linear-gradient(180deg, var(--sky) 0%, var(--mid-blue) 100%); }
  .card__art { position: absolute; inset: 0; }
  .contact {
    position: absolute; right: 34px; top: 50px;
    color: var(--white);
    text-align: right;
    font-size: 19px;
    line-height: 1.35;
  }
  .contact__name { font-weight: 700; font-size: 25px; margin-bottom: 6px; }
  .contact__address { margin-bottom: 14px; }
  .contact__line { display: flex; justify-content: flex-end; align-items: center; gap: 10px; white-space: nowrap; }
  .contact__line svg { width: 16px; height: 16px; flex: none; }
</style>
</head>
<body>
<main class="stage">
  <section class="card card--front" aria-label="Card front">
    <div class="brand">
      <span class="brand__mark"></span>
      <span class="brand__name">Kelvara Pane Works</span>
    </div>
    <ul class="services">
      <li>Shower screens</li><li>Fly screens</li><li>Wardrobe doors</li><br>
      <li>Security doors</li><li>Grilles + mirrors</li>
    </ul>
  </section>

  <section class="card card--back" aria-label="Card back">
    <svg class="card__art" viewBox="0 0 660 378">
      <defs>
        <linearGradient id="emblemFill" x1="0" y1="0" x2="0" y2="1">
          <stop offset="0" stop-color="#5ec4e6"/>
          <stop offset="1" stop-color="#2f7cc2"/>
        </linearGradient>
      </defs>
      <path d="M0 0 H282 C350 70 340 210 215 285 C145 325 70 345 0 360 Z" fill="#000"/>
      <path d="M300 0 C365 80 350 220 225 298 C150 340 75 358 0 370" fill="none" stroke="#000" stroke-width="3"/>
      <circle cx="150" cy="175" r="120" fill="url(#emblemFill)" role="img" aria-label="Cracked glass emblem area"/>
    </svg>
    <div class="contact">
      <p class="contact__name">Malcolm</p>
      <p class="contact__address">17C Tindale Ridge Rd<br>Tindale Bay 7395</p>
      <p class="contact__line">02 48931067
        <svg viewBox="0 0 16 16"><path d="M4 1 L6.5 4.5 L5 6 C6 8.5 7.5 10 10 11 L11.5 9.5 L15 12 L13 15 C7 15 1 9 1 3 Z" fill="#fff"/></svg>
      </p>
      <p class="contact__line">02 48931067
        <svg viewBox="0 0 16 16"><rect x="2" y="6" width="12" height="8" fill="#fff"/><rect x="4" y="2" width="8" height="5" fill="none" stroke="#fff" stroke-width="1.5"/></svg>
      </p>
      <p class="contact__line">0419682350
        <svg viewBox="0 0 16 16"><rect x="4" y="1" width="8" height="14" rx="1.5" fill="none" stroke="#fff" stroke-width="1.5"/><rect x="6" y="3" width="4" height="8" fill="#fff"/></svg>
      </p>
      <p class="contact__line">kelvarapane@fenmail.example
        <svg viewBox="0 0 16 16"><rect x="1" y="3" width="14" height="10" fill="#fff"/><path d="M1 3 L8 9 L15 3" fill="none" stroke="#3a86c8" stroke-width="1.2"/></svg>
      </p>
    </div>
  </section>
</main>
</body>
</html>
```